Modern Attractive Letterhead for Veterinary House Call Business.

A letterhead which can be printed on A4, A5 and A6 paper sizes.
To have: ( our files to be uploaded)
1. Logo with Text
2. telephone
3. email
4. website
5. Address

Target Market(s)

60-85year mainly women pet owners. Also market include families, young professionals, busy people who have dogs and cats

Industry/Entity Type

Business

Requirements
Must have
• 1. Logo with Text ( provided)
• 2. telephone
• 3. email
• 4. website
• 5. Address
Nice to have
• Needs to be modern, preferably warm and caring in nature( if possible )
Should not have
• difficulty in printing A5 and A6

```html
<!DOCTYPE html>
<html lang="en">
<head>
<meta charset="utf-8">
<title>Kindly Vet Visits – Letterhead</title>
<link rel="stylesheet" href="https://fonts.googleapis.com/css2?family=Cinzel:wght@400;600&display=swap">
<style>
  :root {
    --paper-top: #ffffff;
    --paper-bottom: #f1f1f4;
    --brand-blue: #1f3f8f;
    --ink: #3a3a3a;
    --rule: #9a9a9a;
    --icon-green: #4f9d3a;
    --mark-blue: rgba(222, 236, 246, 0.95);
    --mark-grey: rgba(226, 228, 238, 0.75);
    --mark-fade: rgba(230, 231, 238, 0);
  }
  * { margin: 0; padding: 0; box-sizing: border-box; }
  html, body { width: 934px; height: 1200px; overflow: hidden; background: #ffffff; }
  .letterhead {
    position: relative;
    width: 934px;
    height: 1200px;
    background: linear-gradient(160deg, var(--paper-top) 30%, var(--paper-bottom) 100%);
    font-family: "Cinzel", "Times New Roman", serif;
    color: var(--ink);
    overflow: hidden;
  }
  .watermark-area {
    position: absolute;
    left: -80px;
    top: 360px;
    width: 720px;
    height: 900px;
    background: radial-gradient(closest-side ellipse at 50% 45%,
      var(--mark-blue) 0%,
      var(--mark-grey) 45%,
      var(--mark-fade) 100%);
  }
  .brand {
    position: absolute;
    left: 40px;
    top: 64px;
    display: flex;
    align-items: center;
    gap: 16px;
  }
  .brand-dot {
    width: 56px;
    height: 56px;
    border-radius: 50%;
    background: var(--brand-blue);
  }
  .brand-name {
    font-size: 40px;
    font-weight: 400;
    color: var(--brand-blue);
    letter-spacing: 1px;
    line-height: 1;
  }
  .contact {
    position: absolute;
    left: 660px;
    top: 46px;
    padding-left: 10px;
    border-left: 1px solid var(--rule);
    list-style: none;
    font-size: 12.5px;
    line-height: 21px;
    text-transform: uppercase;
    letter-spacing: 0;
  }
  .contact li { display: flex; align-items: center; gap: 6px; white-space: nowrap; }
  .contact svg { width: 11px; height: 11px; flex: none; }
  .address {
    position: absolute;
    left: 482px;
    bottom: 24px;
    transform: translateX(-50%);
    white-space: nowrap;
    font-size: 15px;
    letter-spacing: 0.5px;
  }
</style>
</head>
<body>
  <main class="letterhead">
    <div class="watermark-area" role="img" aria-label="Faint large brand watermark in soft blue and grey"></div>

    <header class="brand">
      <span class="brand-dot"></span>
      <span class="brand-name">Kindly Vet Visits</span>
    </header>

    <ul class="contact">
      <li>
        <svg viewBox="0 0 12 12" aria-hidden="true"><circle cx="6" cy="6" r="5.2" fill="none" stroke="var(--icon-green)" stroke-width="1.2"/><path d="M4 3.3 L5 3 L5.6 4.6 L5 5.1 Q5.6 6.5 6.9 7 L7.4 6.4 L9 7 L8.7 8 Q6.2 8.6 4 5.3 Z" fill="var(--icon-green)"/></svg>
        0412555019
      </li>
      <li>
        <svg viewBox="0 0 12 12" aria-hidden="true"><rect x="1" y="3" width="10" height="7" rx="1" fill="var(--icon-green)"/><path d="M1.5 3.5 L6 7 L10.5 3.5" fill="none" stroke="#fff" stroke-width="1"/></svg>
        info@kindlyvetvisits.com.au
      </li>
      <li>
        <svg viewBox="0 0 12 12" aria-hidden="true"><circle cx="6" cy="6" r="5" fill="none" stroke="var(--icon-green)" stroke-width="1.2"/><ellipse cx="6" cy="6" rx="2.2" ry="5" fill="none" stroke="var(--icon-green)" stroke-width="1"/><path d="M1 6 H11 M2 3.5 H10 M2 8.5 H10" stroke="var(--icon-green)" stroke-width="0.9"/></svg>
        www.kindlyvetvisits.com.au
      </li>
    </ul>

    <footer class="address">PO Box 4521 Brookvale Heights QLD 4071</footer>
  </main>
</body>
</html>
```